We need a business card for our gym. We are a PowerCore affiliate in Decatur Georgie established 2008. Our company name is Rally Functional Fitness. PowerCore Building Prime Fitness. Instagram and website is @rallygym. Hashtags we use #rallywithheart #madetorally We want something similar to the the black and neon green design attached but a different color scheme. No neon colors. Are company colors are the same as the blue and white card attached. We are open to ideas as far as colors however - just no neon.

Contact Information for Business Card

Rally Functional Fitness
472 Halvern Drive
Decatur GA 30041
Phone 404.555.0187 Website www.rallygym.example

Font styles to use
Other font styles liked:
• Futura Extra Bold Condensed

Colors

Designer to choose colors to be used in the design.

Requirements
Must have
• Our primary font we typically use for our name is Futura Extra Bold Condensed
Nice to have
• I attached a card from that is black and neon green from Zorva that we would like something similar. The blue and white is more similar to our colors. We also use have used black and white in the past. We use the chevrons as out logo. We are a PowerCore affiliate so I included a logo from them as well that may or may not be used on the card. Our instagram is @rallygym hashtags #madetorally #rallywithheart
Should not have
• No neon colors

```html
<!DOCTYPE html>
<html lang="en">
<head>
<meta charset="utf-8">
<title>Rally Functional Fitness – Business Card</title>
<link rel="stylesheet" href="https://fonts.googleapis.com/css2?family=Oswald:wght@500;700&family=Montserrat:wght@500&display=swap">
<style>
  :root {
    --backdrop: #2b2b2b;
    --card: #1e1e1e;
    --ink-gloss: #4a4c48;
    --ink-soft: #5c5e5a;
    --ink-light: #a6a8a4;
    --rule: #5a5c58;
  }
  * { margin: 0; padding: 0; box-sizing: border-box; }
  html, body {
    width: 1200px; height: 901px; overflow: hidden;
    background: var(--backdrop);
  }
  .stage {
    position: relative; width: 1200px; height: 901px;
    display: flex; flex-direction: column; align-items: center; justify-content: center; gap: 40px;
  }
  .card {
    position: relative; width: 630px; height: 360px;
    background: var(--card);
    box-shadow: 0 12px 30px rgba(0,0,0,.45);
    overflow: hidden;
  }

  /* Front */
  .brand {
    position: absolute; left: 70px; top: 95px;
    font-family: "Oswald", sans-serif; font-weight: 700;
    color: var(--ink-gloss); text-transform: uppercase; line-height: 1;
  }
  .brand-name { display: flex; align-items: center; gap: 16px; font-size: 92px; letter-spacing: 1px; }
  .brand-mark { width: 26px; height: 26px; background: var(--ink-gloss); }
  .brand-tagline { font-size: 30px; letter-spacing: 1.5px; margin-top: 8px; }

  /* Back */
  .coach {
    position: absolute; left: 40px; top: 120px; width: 260px; text-align: right;
    text-transform: uppercase;
  }
  .coach-name {
    font-family: "Oswald", sans-serif; font-weight: 700; font-size: 34px;
    color: var(--ink-gloss); letter-spacing: .5px; line-height: 1.05;
  }
  .coach-role {
    font-family: "Montserrat", sans-serif; font-weight: 500; font-size: 19px;
    color: var(--ink-soft); letter-spacing: .5px;
  }
  .divider {
    position: absolute; left: 322px; top: 118px; width: 1px; height: 90px; background: var(--rule);
  }
  .contact-list {
    position: absolute; left: 345px; top: 122px; list-style: none;
    font-family: "Montserrat", sans-serif; font-weight: 500; font-size: 18px;
    color: var(--ink-light); line-height: 28px;
  }
  .contact-list li { display: flex; align-items: center; gap: 8px; }
  .contact-list svg { width: 15px; height: 15px; flex: none; fill: var(--ink-light); }
  .address {
    position: absolute; left: 0; right: 0; bottom: 48px; text-align: center;
    font-family: "Montserrat", sans-serif; font-weight: 500; font-size: 20px;
    color: var(--ink-soft);
  }
</style>
</head>
<body>
<main class="stage">
  <section class="card card-front" aria-label="Card front">
    <div class="brand">
      <div class="brand-name"><span>Rally</span><span class="brand-mark"></span></div>
      <div class="brand-tagline">Functional Fitness</div>
    </div>
  </section>

  <section class="card card-back" aria-label="Card back">
    <div class="coach">
      <p class="coach-name">Marcus Adell</p>
      <p class="coach-role">Expert Coaches</p>
    </div>
    <div class="divider"></div>
    <ul class="contact-list">
      <li>
        <svg viewBox="0 0 24 24" aria-hidden="true"><path d="M6.6 10.8a15.1 15.1 0 0 0 6.6 6.6l2.2-2.2a1 1 0 0 1 1-.25 11.4 11.4 0 0 0 3.6.57 1 1 0 0 1 1 1V20a1 1 0 0 1-1 1A17 17 0 0 1 3 4a1 1 0 0 1 1-1h3.5a1 1 0 0 1 1 1c0 1.25.2 2.45.57 3.57a1 1 0 0 1-.25 1z"/></svg>
        404.555.0187
      </li>
      <li>
        <svg viewBox="0 0 24 24" aria-hidden="true"><path d="M2 5h20v14H2zm2 2v.5l8 5 8-5V7zm0 2.8V17h16V9.8l-8 5z"/></svg>
        info@rallygym.example
      </li>
      <li>
        <svg viewBox="0 0 24 24" aria-hidden="true"><circle cx="12" cy="12" r="10"/></svg>
        www.rallygym.example
      </li>
    </ul>
    <p class="address">472 Halvern Drive, Decatur GA 30041</p>
  </section>
</main>
</body>
</html>
```